Redesign Our Presentation on Rational Prescribing

We are looking for a new designer for KVMed, a project that creates educational modules for healthcare providers in the District of Columbia (more information at healthbureau-example.org/kvmed). We want someone to redesign our powerpoints to look clean and professional, with original graphics that reflect the content on the slides. We also want someone who is creative and could potentially also redesign factsheets, written reports, and promotional postcards.

All the text on the slides must stay the same and it must be in the template (red line at the top, with the red box at the bottom, with the Halvern Bureau of Health logo). We want a powerpoint that features original graphics, looks professional, looks clean and is easy to read.

```html
<!DOCTYPE html>
<html lang="en">
<head>
<meta charset="utf-8">
<title>Consequences of Multiple Medication Use</title>
<link rel="stylesheet" href="https://fonts.googleapis.com/css2?family=Arimo:wght@400;700&display=swap">
<style>
  :root {
    --ink: #3a3a3a;
    --body: #333333;
    --red: #e8202a;
    --band: #f41c1c;
    --track: #dcdcdc;
    --gold: #b9955a;
    --navy: #2b2a7c;
    --white: #ffffff;
  }
  * { margin: 0; padding: 0; box-sizing: border-box; }
  html, body { width: 1200px; height: 675px; overflow: hidden; background: var(--white); }
  body { font-family: "Arimo", Arial, sans-serif; color: var(--body); }
  .slide { position: relative; width: 1200px; height: 675px; overflow: hidden; }

  .slide-title {
    position: absolute; left: 85px; top: 106px;
    font-size: 37px; font-weight: 700; color: var(--ink); letter-spacing: -0.2px;
  }
  .title-rule {
    position: absolute; left: 85px; right: 0; top: 161px;
    height: 2px; background: var(--red);
  }

  .brand {
    position: absolute; right: 40px; top: 52px;
    display: flex; align-items: center; gap: 10px;
  }
  .brand-mark { width: 22px; height: 22px; background: var(--navy); }
  .brand-name {
    width: 150px; font-size: 18px; font-weight: 700; line-height: 1.15; color: var(--navy);
  }

  .lead {
    position: absolute; left: 96px; top: 185px; width: 1060px;
    display: flex; gap: 16px; font-size: 20px; line-height: 1.2;
  }
  .lead-bullet { flex: none; width: 10px; height: 13px; margin-top: 4px; border: 1.5px solid var(--body); }

  .stat-label {
    position: absolute; width: 220px; bottom: 353px;
    text-align: center; font-size: 17.5px; line-height: 1.4; color: var(--body);
  }
  .stat-rule { position: absolute; top: 322px; width: 200px; height: 1px; background: var(--gold); }
  .stat-tick { position: absolute; top: 322px; width: 1px; height: 32px; background: var(--gold); }
  .stat-chart { position: absolute; top: 331px; width: 300px; height: 300px; }
  .stat-value {
    position: absolute; top: 451px; width: 220px; text-align: center;
    font-size: 52px; font-weight: 700; color: var(--red);
    text-shadow: 2px 3px 4px rgba(0,0,0,0.35);
  }

  .footer {
    position: absolute; left: 0; right: 0; bottom: 0; height: 50px;
    background: var(--band); color: var(--white);
    display: flex; align-items: center; justify-content: space-between;
    padding: 0 44px 0 78px;
  }
  .page-number { font-size: 16px; }
  .footer-url { font-size: 20px; }
</style>
</head>
<body>
<main class="slide">
  <div class="brand">
    <span class="brand-mark"></span>
    <span class="brand-name">Halvern Bureau of Health</span>
  </div>

  <h1 class="slide-title">Consequences of Multiple Medication Use</h1>
  <div class="title-rule"></div>

  <p class="lead">
    <span class="lead-bullet"></span>
    <span>The use of several medications simultaneously, even at otherwise appropriate doses, increases the risk of adverse effects, drug interactions, non-adherence, and death.</span>
  </p>

  <svg width="0" height="0" style="position:absolute">
    <defs>
      <marker id="gold-arrow" viewBox="0 0 10 10" refX="6" refY="5" markerWidth="7" markerHeight="7" orient="auto">
        <path d="M0 0 L10 5 L0 10 z" fill="#b9955a"/>
      </marker>
    </defs>
  </svg>

  <!-- Two medicines -->
  <p class="stat-label" style="left:109px">The risk of ADRs when taking two medicines</p>
  <div class="stat-rule" style="left:119px"></div>
  <div class="stat-tick" style="left:219px"></div>
  <svg class="stat-chart" style="left:69px" viewBox="-150 -150 300 300" aria-label="Donut chart showing 13 percent">
    <circle r="115" fill="none" stroke="var(--track)" stroke-width="17"/>
    <circle r="103" fill="none" stroke="var(--red)" stroke-width="46" pathLength="100" stroke-dasharray="13 100" transform="rotate(-90)"/>
    <path d="M0 -128 A128 128 0 0 1 93.3 -87.7" fill="none" stroke="var(--gold)" stroke-width="1.5" marker-end="url(#gold-arrow)"/>
  </svg>
  <p class="stat-value" style="left:109px">13%</p>

  <!-- Five medicines -->
  <p class="stat-label" style="left:486px">The risk of ADRs when taking five medicines</p>
  <div class="stat-rule" style="left:496px"></div>
  <div class="stat-tick" style="left:596px"></div>
  <svg class="stat-chart" style="left:446px" viewBox="-150 -150 300 300" aria-label="Donut chart showing 58 percent">
    <circle r="115" fill="none" stroke="var(--track)" stroke-width="17"/>
    <circle r="103" fill="none" stroke="var(--red)" stroke-width="46" pathLength="100" stroke-dasharray="58 100" transform="rotate(-90)"/>
    <path d="M0 -128 A128 128 0 1 1 -61.7 112.1" fill="none" stroke="var(--gold)" stroke-width="1.5" marker-end="url(#gold-arrow)"/>
  </svg>
  <p class="stat-value" style="left:486px">58%</p>

  <!-- Seven medicines -->
  <p class="stat-label" style="left:890px">The risk of ADRs when taking seven medicines (Marlowe 2015)</p>
  <div class="stat-rule" style="left:900px"></div>
  <div class="stat-tick" style="left:1000px"></div>
  <svg class="stat-chart" style="left:850px" viewBox="-150 -150 300 300" aria-label="Donut chart showing 82 percent">
    <circle r="115" fill="none" stroke="var(--track)" stroke-width="17"/>
    <circle r="103" fill="none" stroke="var(--red)" stroke-width="46" pathLength="100" stroke-dasharray="82 100" transform="rotate(-90)"/>
    <path d="M0 -128 A128 128 0 1 1 -115.8 -54.5" fill="none" stroke="var(--gold)" stroke-width="1.5" marker-end="url(#gold-arrow)"/>
  </svg>
  <p class="stat-value" style="left:890px">82%</p>

  <footer class="footer">
    <span class="page-number">2</span>
    <span class="footer-url">www.healthbureau-example.org</span>
  </footer>
</main>
</body>
</html>
```